HKR Slab Chats

- Brochure design

Target Market(s)

Granite and Quartz

Font styles to use
Sans Serif

Colors

Designer to choose colors to be used in the design.

Requirements
Must have
• I post the instruction file below
Nice to have
Should not have

```html
<!DOCTYPE html>
<html lang="en">
<head>
<meta charset="utf-8">
<title>HKR Slab Chats – Granite Brochure Spread</title>
<link href="https://fonts.googleapis.com/css2?family=Source+Sans+3:wght@400;600&display=swap" rel="stylesheet">
<style>
  :root {
    --page-bg: #ffffff;
    --band: #3a312c;
    --rule: #e9e4df;
    --ink-light: #f4f1ec;
    --ink-body: #e6e0d8;
    --panel-left: rgba(72, 64, 58, 0.88);
    --panel-right: rgba(52, 44, 39, 0.86);
    --photo-top: #d8c99a;
    --photo-mid: #c9b98f;
    --photo-low: #6b5440;
    --photo-floor: #4a382a;
  }
  * { margin: 0; padding: 0; box-sizing: border-box; }
  html, body {
    width: 1200px; height: 900px; overflow: hidden;
    background: var(--page-bg);
    font-family: "Source Sans 3", sans-serif;
  }
  .spread {
    position: absolute; left: 80px; top: 68px;
    width: 1040px; height: 764px;
    background: var(--band);
    overflow: hidden;
  }
  .header-rule {
    position: absolute; left: 0; top: 106px; width: 100%; height: 1px;
    background: var(--rule);
  }
  .gutter {
    position: absolute; left: 520px; top: 0; width: 1px; height: 127px;
    background: rgba(255,255,255,0.25);
  }
  .brand {
    position: absolute; left: 40px; top: 50px; color: var(--ink-light);
  }
  .brand-name { font-size: 28px; font-weight: 400; line-height: 1; letter-spacing: 0.3px; }
  .brand-tagline { font-size: 10px; margin-top: 4px; }
  .section-title {
    position: absolute; right: 33px; top: 66px;
    font-size: 30px; font-weight: 400; color: var(--ink-light); line-height: 1;
  }
  .photo {
    position: absolute; left: 0; top: 127px; width: 1037px; height: 637px;
    background: linear-gradient(180deg, var(--photo-top) 0%, var(--photo-mid) 40%, var(--photo-low) 75%, var(--photo-floor) 100%);
  }
  .intro-panel {
    position: absolute; left: 4px; top: 419px; width: 289px; height: 300px;
    background: var(--panel-left);
    padding: 40px 36px 0 39px;
    color: var(--ink-light); font-size: 12.4px; line-height: 16.6px;
  }
  .body-column {
    position: absolute; left: 557px; top: 127px; width: 223px; height: 637px;
    background: var(--panel-right);
    padding: 22px 16px 0 17px;
    color: var(--ink-body); font-size: 8.6px; font-weight: 400; line-height: 11.7px;
  }
  .body-column p + p { margin-top: 11.7px; }
  .folio {
    position: absolute; top: 739px; color: var(--ink-light);
    display: flex; align-items: baseline; gap: 6px;
  }
  .folio-number { font-size: 13px; }
  .folio-url { font-size: 8.5px; }
  .folio-left { left: 12px; }
  .folio-right { right: 10px; }
</style>
</head>
<body>
  <div class="spread">
    <div class="brand">
      <div class="brand-name">HKR Slab Chats</div>
      <div class="brand-tagline">Crafted Surfaces, Lasting Finish</div>
    </div>
    <h1 class="section-title">Granite</h1>
    <div class="header-rule"></div>
    <div class="gutter"></div>

    <div class="photo" role="img" aria-label="Bright kitchen with cream cabinets, granite island countertops, stainless steel ovens and refrigerator, and dark wood floor"></div>

    <div class="intro-panel">
      Lorem ipsum dolor sit amet. Iriure est diam voluptua justo duis diam. Est nonumy et lorem eum. Eros nonummy sea stet eos nostrud sit tempor. Ipsum no justo facilisi. Lorem augue dolores eos takimata kasd sed. Et vero suscipit. Vel veniam dolor exerci est esse luptatum. Lobortis kasd et clita et feugiat sed cum. Dolore eos nulla. Eros dolore eos esse adipiscing sit. Elitr est iriure et consetetur. Magna at in magna labore feugiat. Dolores labore laoreet amet no.
    </div>

    <div class="body-column">
      <p>Lorem ipsum dolor sit amet. Takimata et quis et amet. Ut stet nostrud aliquyam consequat eleifend vulputate. Consetetur at velit rebum vero rebum ipsum duo. Facer et dolore. Ea delenit eum sit elit blandit erat sanctus. Et sit sed. Sanctus aliquip cum odio amet. Velit invidunt amet sed sanctus est. Diam ad ipsum sed eros vel magna. Clita nulla stet at. Sed aliquyam delenit justo. Stet sed nostrud gubergren esse consetetur. Nulla diam amet id duis odio amet feugiat. Ea volutpat eirmod eos justo minim eirmod. Ullamcorper elit clita ut facilisi aliquyam eirmod. Sanctus lorem vero. Gubergren sadipscing facilisi.</p>
      <p>Minim ipsum feugiat enim. Autem accusam consetetur et duo voluptua. Vero no diam duo eros sed. Lorem ex sed eu consequat duo erat sed. Ea nam nonumy invidunt eu ipsum mazim dolor. Gubergren dolor sed duis dolor mazim accusam. Ut takimata et. Minim no euismod magna. Molestie ipsum ullamcorper autem sit. No iusto sed ut sadipscing. Dolor clita gubergren wisi euismod luptatum. Dolore aliquip dolor. Duis voluptua iusto sadipscing et laoreet. Consetetur et lobortis et hendrerit dolore eos et. Accusam nonumy erat nulla delenit. Takimata et rebum lorem. Nibh invidunt id takimata kasd volutpat.</p>
      <p>Consetetur voluptua duis nam et amet. Et praesent ea. Luptatum diam ut et voluptua sed labore iriure. Dolor nonumy dolore qui dolore lorem. Diam commodo diam facilisi ullamcorper volutpat lorem. Duo gubergren diam. Tempor nonummy lorem et no consequat aliquyam hendrerit. Aliquip nonumy lobortis diam facilisis. Accumsan eos illum autem. Odio cum eos veniam est dolore. Dolore ipsum diam. Sanctus rebum soluta sit vel nonumy sanctus ipsum. Accusam molestie et.</p>
      <p>Elit et takimata duo facilisi. Sanctus ut aliquyam et nonummy clita. Elitr tempor ut elit exerci luptatum elit accumsan. Dolor diam dolores odio amet et nonummy. Clita commodo ut no sit blandit ut. Est option eirmod wisi et clita nonumy. Consequat at dolores sea. Invidunt stet esse et te consetetur stet. Nam delenit invidunt.</p>
    </div>

    <div class="folio folio-left">
      <span class="folio-number">01</span>
      <span class="folio-url">www.hkrsurfaces.net</span>
    </div>
    <div class="folio folio-right">
      <span class="folio-url">www.hkrsurfaces.net</span>
      <span class="folio-number">02</span>
    </div>
  </div>
</body>
</html>
```